One of a kind, 100% Pure & Natural Skincare line needs stunning product label

We need product label design for new natural skincare company called Tolven & Mira Skincare. We create luxurious, 100% pure & natural skincare that is free from ingredients that may be potentially irritating to the skin. No toxins, preservatives or additives. Our initial product is Harbor Face Balm, a nourishing face cream that suits discerning women with mature skin and those with dry/sensitive skin needing extra hydration. Also those that choose to minimize their exposure to environmental toxins. Our brand is simple yet elegant, supporting a holistic, authentic lifestyle and GENTLE CARE FOR MATURE SKIN.

Target Market(s)

Discerning women with mature skin and those with dry/sensitive skin needing extra hydration. Also those that choose to minimize their exposure to environmental toxins.

Industry/Entity Type

Skin Care Product

Font styles to use
Sans Serif
Script

Colors
f9d9e8
fef1ee

Requirements
Must have
• The Logo.
HARBOR FACE BALM
GENTLE CARE FOR MATURE SKIN
Labels must be feminine, simple/minimal yet stylish. Uncluttered yet elegant.
This is a very natural product with minimal ingredients.
Nice to have
• The logo can be incorporated in to the label, or It can be left separate as a sticker on top of the jar. The product is a firm balm consistency and is in frosted glass jars with matt silver lids.
Jar height is 45mm, width is 60mm.
Label height: 28mm and length 185mm
Should not have
• Natural or farmers market type theme. No Bold/loud lettering.

```html
<!DOCTYPE html>
<html lang="en">
<head>
<meta charset="utf-8">
<title>Harbor Face Balm – Label</title>
<link rel="stylesheet" href="https://fonts.googleapis.com/css2?family=Montserrat:wght@400;500;600&display=swap">
<style>
  :root {
    --ink: #231f20;
    --pink-deep: #f2bccd;
    --pink-soft: #f9d9e8;
    --blush: #fef1ee;
    --white: #ffffff;
    --guide: #9fd6e6;
    --trim: #c9c9c9;
  }
  * { box-sizing: border-box; margin: 0; padding: 0; }
  html, body { width: 1200px; height: 1000px; overflow: hidden; background: var(--white); }
  body { font-family: "Montserrat", Arial, sans-serif; color: var(--ink); position: relative; }

  .bleed-guide {
    position: absolute; left: 40px; top: 398px; width: 1132px; height: 204px;
    border: 1px dashed var(--guide);
  }
  .label {
    position: absolute; left: 58px; top: 417px; width: 1095px; height: 165px;
    border: 1px solid var(--trim); background: var(--white); overflow: hidden;
  }
  .safe-guide {
    position: absolute; left: 18px; top: 18px; width: 1059px; height: 130px;
    border: 1px dashed var(--guide); pointer-events: none; z-index: 3;
  }
  .front-panel {
    position: absolute; left: 349px; top: 0; width: 385px; height: 100%;
    background: linear-gradient(90deg, var(--pink-deep) 0%, var(--pink-soft) 35%, var(--blush) 70%, var(--white) 100%);
  }
  .leaf-art {
    position: absolute; left: 40px; top: 28px; width: 120px; height: 130px;
    border-radius: 60% 40% 50% 50%;
    background: linear-gradient(160deg, rgba(255,255,255,0.35), rgba(255,255,255,0.12));
  }
  .flower-art {
    position: absolute; left: 290px; top: 20px; width: 34px; height: 34px; border-radius: 50%;
    background: radial-gradient(circle, #f6c9d6 0 18%, #ffffff 22% 100%);
  }
  .product-name {
    position: absolute; left: 0; width: 100%; top: 58px; text-align: center;
    font-weight: 400; font-size: 19px; letter-spacing: 1.5px;
  }
  .tagline {
    position: absolute; left: 0; width: 100%; top: 86px; text-align: center;
    font-weight: 400; font-size: 7.5px; letter-spacing: 1px;
  }
  .net-wt {
    position: absolute; left: 0; width: 100%; top: 129px; text-align: center;
    font-size: 5.5px; font-weight: 500;
  }

  .info { position: absolute; font-size: 9.6px; line-height: 1.3; }
  .info b { font-weight: 600; }
  .info p { margin-bottom: 12px; }
  .info-left { left: 24px; top: 25px; width: 320px; }
  .info-left .note { margin-top: 20px; }
  .info-right { left: 753px; top: 23px; width: 300px; }
  .info-right p { margin-bottom: 9px; }
  .contact { display: flex; align-items: center; gap: 4px; }

  .sprig-art {
    position: absolute; border-radius: 50%;
    background: radial-gradient(circle, rgba(196,196,196,0.45), rgba(196,196,196,0.05) 70%);
  }
  .sprig-left { left: 18px; top: 88px; width: 26px; height: 22px; opacity: 0.4; }
  .sprig-right { left: 1025px; top: 68px; width: 40px; height: 38px; }
  .pao-icon { position: absolute; left: 1040px; top: 121px; }
</style>
</head>
<body>
  <div class="bleed-guide"></div>
  <section class="label">
    <div class="safe-guide"></div>

    <div class="info info-left">
      <p><b>INGREDIENTS :</b> &nbsp;Tallow from pasture raised goats, frankincense, sandalwood &amp; myrrh essential oils.</p>
      <p><b>DIRECTIONS :</b> &nbsp;Soften small amount in palm of<br>hand &amp; gently massage into skin as often as</p>
      <p class="note">Allergy patch test recommended. If irritation occurs, discon-<br>tinue use.</p>
    </div>
    <div class="sprig-art sprig-left" role="img" aria-label="Faint leafy sprig decoration"></div>

    <div class="front-panel">
      <div class="leaf-art" role="img" aria-label="Soft pale pink leaf illustration"></div>
      <div class="flower-art" role="img" aria-label="White blossom illustration"></div>
      <h1 class="product-name">HARBOR FACE BALM</h1>
      <p class="tagline">GENTLE CARE FOR MATURE SKIN</p>
      <p class="net-wt">NET WT 1.76 oz</p>
    </div>

    <div class="info info-right">
      <p><b>CAUTION:</b> &nbsp;Keep out of reach of children. If pregnant or breastfeeding, consult your healthcare practitioner. Avoid contact with eyes &amp; sensitive areas.</p>
      <p>Store below 25°C</p>
      <p>MADE IN AUSTRALIA</p>
      <p>B#</p>
      <p class="contact">
        <svg width="13" height="9" viewBox="0 0 13 9" aria-hidden="true"><rect x="0.5" y="0.5" width="12" height="8" fill="none" stroke="#231f20"/><path d="M0.5 0.5 L6.5 5 L12.5 0.5" fill="none" stroke="#231f20"/></svg>
        info@tolvenmiraskincare.com.au
      </p>
    </div>
    <div class="sprig-art sprig-right" role="img" aria-label="Faint grey leafy sprig decoration"></div>
    <svg class="pao-icon" width="22" height="20" viewBox="0 0 22 20" aria-label="Period after opening 6 months">
      <path d="M3 6 L19 6 L19 18 L3 18 Z" fill="none" stroke="#231f20" stroke-width="1.2"/>
      <path d="M3 5 L7 1 L19 1 L15 5" fill="none" stroke="#231f20" stroke-width="1.2"/>
      <text x="11" y="15.5" text-anchor="middle" font-family="Montserrat, sans-serif" font-size="6" font-weight="600" fill="#231f20">6M</text>
    </svg>
  </section>
</body>
</html>
```